New eyelid plastic surgery office needs a business card design-Eyelid Care Partners of the Brenton

I recently used PixelForge for my logo design and was very pleased with creativity and results. It was a difficult decision for me. Now I would like to create a business card based on this logo, which I will attach.

The text should be easily legible as some of my patients have difficulty seeing, but I would like a subtle, sophisticated artistry also evident to make the card memorable. Would like the card based on a similar color scheme as the logo but the inverse or other complementary colors may prove interesting
Updates

A good question was asked...my concern about my visually impaired patients was really my desire to avoid italicized or calligraphic type fonts that may be hard to read. Standard font size for a business card would be fine. Thanks!

Thank you so much for the great work so far. I wanted to give you my particular contact information to see if that would change the look of the cards. Martin Delacourt, MD Address: 2718 Harborview Lane, Suite 206 Wilmington, NC 28517 Phone: 910-555-0193 Fax: 910-555-0194 Website: www.brentonlidstudio.example Please delete the email slot from the card. Thanks so much!

Industry/Entity Type

Plastic

```html
<!DOCTYPE html>
<html lang="en">
<head>
<meta charset="utf-8">
<title>Eyelid Care Partners of the Brenton – Business Card</title>
<link rel="stylesheet" href="https://fonts.googleapis.com/css2?family=Tenor+Sans&family=Open+Sans:wght@600;700&display=swap">
<style>
  :root {
    --backdrop: #0f3a44;
    --card-white: #ffffff;
    --card-edge: #3f6fb8;
    --card-mid: #c9d9f0;
    --brand-blue: #0c3f8f;
    --band-navy: #0a1f7a;
    --band-blue: #1530d6;
    --band-gold: #c9a640;
    --ink: #111111;
    --rule: #333333;
  }
  * { margin: 0; padding: 0; box-sizing: border-box; }
  html, body {
    width: 1200px;
    height: 888px;
    overflow: hidden;
    background: var(--backdrop);
  }
  .business-card {
    position: absolute;
    left: 110px;
    top: 164px;
    width: 980px;
    height: 560px;
    background: radial-gradient(ellipse 70% 75% at 50% 48%, var(--card-white) 45%, var(--card-mid) 78%, var(--card-edge) 100%);
    box-shadow: 0 14px 30px rgba(0, 0, 0, 0.45);
    overflow: hidden;
  }
  .brand-name {
    position: absolute;
    top: 42px;
    left: 0;
    width: 100%;
    text-align: center;
    font-family: "Tenor Sans", sans-serif;
    font-weight: 400;
    color: var(--brand-blue);
    text-transform: uppercase;
    line-height: 1;
  }
  .brand-name .brand-line-main {
    display: block;
    font-size: 66px;
    letter-spacing: 1px;
  }
  .brand-name .brand-line-sub {
    display: block;
    margin-top: 8px;
    font-size: 31px;
    letter-spacing: 1px;
  }
  .ornament-band {
    position: absolute;
    top: 196px;
    left: 0;
    width: 100%;
    height: 72px;
    border-top: 4px solid #b9bcc6;
    border-bottom: 4px solid #b9bcc6;
    background: linear-gradient(90deg, var(--band-navy), var(--band-blue) 30%, var(--band-blue) 70%, var(--band-navy));
  }
  .ornament-band svg { display: block; width: 100%; height: 100%; }
  .contact-block {
    position: absolute;
    left: 70px;
    top: 300px;
    padding-left: 22px;
    border-left: 2px solid var(--rule);
    font-family: "Open Sans", sans-serif;
    color: var(--ink);
  }
  .contact-label {
    font-size: 21px;
    font-weight: 700;
    font-style: normal;
    margin-bottom: 14px;
  }
  .contact-person {
    font-size: 34px;
    font-weight: 700;
    margin: 0 0 14px 100px;
  }
  .contact-details {
    display: grid;
    grid-template-columns: 108px auto;
    row-gap: 4px;
    font-size: 20px;
    font-weight: 600;
    line-height: 1.25;
  }
  .contact-details dt::after { content: ""; }
  .contact-details dd::before { content: ": "; }
</style>
</head>
<body>
  <article class="business-card">
    <h1 class="brand-name">
      <span class="brand-line-main">Eyelid Care Partners</span>
      <span class="brand-line-sub">of the Brenton</span>
    </h1>

    <div class="ornament-band">
      <svg role="img" aria-label="Repeating ornamental border of stylised gold eyes linked by interwoven gold ribbons on a blue band" viewBox="0 0 980 64" preserveAspectRatio="none">
        <rect x="0" y="0" width="980" height="64" fill="url(#bandTone)"/>
        <defs>
          <linearGradient id="bandTone" x1="0" y1="0" x2="0" y2="1">
            <stop offset="0" stop-color="#1530d6" stop-opacity="0"/>
            <stop offset="0.5" stop-color="#c9a640" stop-opacity="0.18"/>
            <stop offset="1" stop-color="#1530d6" stop-opacity="0"/>
          </linearGradient>
        </defs>
      </svg>
    </div>

    <section class="contact-block">
      <p class="contact-label">Contact :</p>
      <h2 class="contact-person">Martin Delacourt, MD</h2>
      <dl class="contact-details">
        <dt>Address</dt><dd>2718 Harborview Lane, Suite 206 Wilmington, NC 28517</dd>
        <dt>Phone</dt><dd>910 - 555 - 0193</dd>
        <dt>Fax</dt><dd>910 - 555 - 0194</dd>
        <dt>web</dt><dd>www.brentonlidstudio.example</dd>
      </dl>
    </section>
  </article>
</body>
</html>
```